Patent Law

Need to develop a home page for a patent lawyer.

Colors should go with logo, blues...

Company Name- Velun Tresk, PLLC

Company Overview-

I am an Intellectual Property Lawyer and focus on patents, copyrights, trademarks, & trade secrets. I work with small businesses and start ups in the chemical and biotech industries.

Why Us-

I am small firm that can provide large-firm service at a reasonable price. I also can charge flat-fees for entreprenuers in certain practice areas.

Services-
Intellectual Property
Patents
Copyrights
Trademarks
Trade secrets
Healthcare Compliance
Elder law
Wills
Trusts

Website we like-
http://www.quorvantlegal.example/ - within industry!!
http://www.daltrowemiko.example/
http://ulbrixtane.example/
http://thegravelcounsel.example/

Target Market(s)

My customers will be small business, specifically small start-up companies in the chemical and biotech arena.

Industry/Entity Type

Trade

Requirements
Must have
• Colors should go with logo, blues...

```html
<!DOCTYPE html>
<html lang="en">
<head>
<meta charset="utf-8">
<title>Velun Tresk, PLLC – Patent Law</title>
<link rel="stylesheet" href="https://fonts.googleapis.com/css2?family=Cinzel:wght@400;600&family=Open+Sans:wght@400;600;700&display=swap">
<style>
:root{
  --blue:#0d6eb5;
  --navy:#1d3f8a;
  --text:#6f6f6f;
  --dark-text:#3c3c3c;
  --banner:#f3f3f3;
  --footer:#2a2a2a;
  --footer-text:#e6e6e6;
  --footer-head:#1a8fd6;
  --white:#ffffff;
}
*{box-sizing:border-box;margin:0;padding:0}
html,body{width:1169px;height:1200px;overflow:hidden;background:var(--white)}
body{position:relative;font-family:"Open Sans",Arial,sans-serif;color:var(--text)}
ul{list-style:none}
.abs{position:absolute}

/* header */
.brand{left:126px;top:32px;display:flex;align-items:center;gap:10px}
.brand-dot{width:30px;height:30px;border-radius:50%;background:var(--blue)}
.brand-name{font-family:"Cinzel",serif;font-weight:600;font-size:17px;color:#555d66;letter-spacing:.5px;margin-top:42px}
.header-phone{left:868px;top:52px;font-family:"Cinzel",serif;font-size:15px;color:var(--blue)}
.header-phone span{color:#333;margin:0 6px}
.globe{left:982px;top:45px;width:58px;height:30px;border-radius:50%;background:radial-gradient(ellipse at 40% 40%,#39a6f0,#0b74c9)}
.main-nav{left:420px;top:94px;display:flex;gap:0}
.main-nav a{font-family:"Cinzel",serif;font-size:15px;color:var(--navy);text-decoration:none;margin-right:32px}
.main-nav a:last-child{margin-right:0}

/* banner */
.hero{left:117px;top:127px;width:935px;height:359px;background:var(--banner)}
.hero-arrow{top:162px}
.hero-title{left:82px;top:98px;font-size:20px;font-weight:600;color:var(--blue)}
.hero-copy{left:81px;top:136px;width:420px;font-size:12.3px;line-height:27.3px}
.hero-btn{left:80px;top:249px;width:148px;height:45px;background:var(--blue);color:var(--white);font-size:12px;font-weight:600;display:flex;align-items:center;justify-content:center}
.hero-photo{left:521px;top:0;width:330px;height:359px;background:linear-gradient(180deg,#ececec 0%,#d9c2b0 25%,#3a3d44 45%,#23262c 100%)}

/* columns */
.col{top:526px;width:293px}
.col-title{font-family:"Cinzel",serif;font-size:13.5px;color:var(--navy);letter-spacing:.5px;height:29px}
.col-photo{height:156px}
.why-copy{margin-top:8px;font-size:12.3px;line-height:23.4px;color:#4d4d4d}
.service-grid{margin-top:8px;display:grid;grid-template-columns:150px 150px;row-gap:11px;font-size:12px}
.service-grid li{display:flex;align-items:center;gap:10px;height:24px;line-height:24px}
.chev{width:6px;height:10px}
.contact-name{margin-top:12px;font-size:15px;font-weight:700;color:var(--blue)}
.contact-list{margin-top:2px;font-size:12.3px;line-height:23.4px;color:#555}

/* footer */
.site-footer{left:0;top:914px;width:1169px;height:286px;background:var(--footer)}
.fcol{top:25px}
.fcol h3{font-size:15px;font-weight:400;color:var(--footer-head);margin-bottom:17px}
.fcol li{font-size:12.3px;color:var(--footer-text);line-height:23.4px}
.news-copy{font-size:12.3px;line-height:19.5px;color:var(--footer-text);width:220px}
.field{width:215px;height:26px;background:var(--white);border:1px solid #ccc;font-size:11.5px;color:#b5b5b5;padding-left:13px;line-height:24px}
.subscribe{width:96px;height:23px;border-radius:12px;background:#1187d6;color:var(--white);font-size:12.5px;font-weight:600;text-align:center;line-height:23px}
.social li{display:flex;align-items:center;justify-content:space-between;width:134px;height:27px;margin-bottom:10px}
.social-dot{width:26px;height:26px;border-radius:50%;background:var(--white)}
.copyright{left:465px;top:264px;font-size:12px;color:var(--white);letter-spacing:-.2px}
</style>
</head>
<body>

<header>
  <div class="abs brand"><div class="brand-dot"></div><div class="brand-name">VELUN TRESK, PLLC</div></div>
  <div class="abs header-phone">1-800-555-0142<span>|</span></div>
  <div class="abs globe" role="img" aria-label="Blue world map icon"></div>
  <nav class="abs main-nav">
    <a href="#">Home</a><a href="#">About Us</a><a href="#">Services</a><a href="#">Practices</a><a href="#">News</a><a href="#">FAQ's</a><a href="#">Contact US</a>
  </nav>
</header>

<section class="abs hero">
  <svg class="abs hero-arrow" style="left:12px" width="26" height="40" viewBox="0 0 26 40"><path d="M22 3 L6 20 L22 37" fill="none" stroke="#fff" stroke-width="6"/></svg>
  <svg class="abs hero-arrow" style="left:898px" width="26" height="40" viewBox="0 0 26 40"><path d="M4 3 L20 20 L4 37" fill="none" stroke="#fff" stroke-width="6"/></svg>
  <h1 class="abs hero-title">Velun Tresk</h1>
  <p class="abs hero-copy">Lorem Ipsum is simply dummy text of the printing and typesetting industry. Lorem Ipsum has been the industry's standard dummy text ever since the 1500s, when an unknown printer took a galley of type and scrambled it to make a type specimen book</p>
  <div class="abs hero-btn">Learn More</div>
  <div class="abs hero-photo" role="img" aria-label="Smiling attorney in a dark suit with arms crossed"></div>
</section>

<section class="abs col" style="left:127px">
  <h2 class="col-title">Why Us</h2>
  <div class="col-photo" role="img" aria-label="Hand pointing at a network of people icons on blue" style="background:linear-gradient(135deg,#4f97d6,#2f79bd)"></div>
  <p class="why-copy">Lorem Ipsum is simply dummy text of the printing and typesetting industry. Lorem Ipsum has been the industry's standard dummy text ever since the 1500s, when an unknown printer took a galley of type and scrambled it to make a type specimen book. It has survived not only five centuries, but also the leap into electronic typesetting</p>
</section>

<section class="abs col" style="left:438px">
  <h2 class="col-title">WHAT WE DO ?</h2>
  <div class="col-photo" role="img" aria-label="Team meeting around a white table seen from above" style="background:linear-gradient(135deg,#8a8a8a,#c9c9c9 50%,#7d7d7d)"></div>
  <ul class="service-grid">
    <li><svg class="chev" viewBox="0 0 6 10"><path d="M1 1l4 4-4 4" fill="none" stroke="#222" stroke-width="1.8"/></svg>Intellectual Property</li>
    <li><svg class="chev" viewBox="0 0 6 10"><path d="M1 1l4 4-4 4" fill="none" stroke="#222" stroke-width="1.8"/></svg>Healthcare Compliance</li>
    <li><svg class="chev" viewBox="0 0 6 10"><path d="M1 1l4 4-4 4" fill="none" stroke="#222" stroke-width="1.8"/></svg>Patents</li>
    <li><svg class="chev" viewBox="0 0 6 10"><path d="M1 1l4 4-4 4" fill="none" stroke="#222" stroke-width="1.8"/></svg>Elder law</li>
    <li><svg class="chev" viewBox="0 0 6 10"><path d="M1 1l4 4-4 4" fill="none" stroke="#222" stroke-width="1.8"/></svg>Copyrights</li>
    <li><svg class="chev" viewBox="0 0 6 10"><path d="M1 1l4 4-4 4" fill="none" stroke="#222" stroke-width="1.8"/></svg>Wills</li>
    <li><svg class="chev" viewBox="0 0 6 10"><path d="M1 1l4 4-4 4" fill="none" stroke="#222" stroke-width="1.8"/></svg>Trademarks</li>
    <li><svg class="chev" viewBox="0 0 6 10"><path d="M1 1l4 4-4 4" fill="none" stroke="#222" stroke-width="1.8"/></svg>Trusts</li>
    <li><svg class="chev" viewBox="0 0 6 10"><path d="M1 1l4 4-4 4" fill="none" stroke="#222" stroke-width="1.8"/></svg>Trade secrets</li>
  </ul>
</section>

<section class="abs col" style="left:750px">
  <h2 class="col-title">CONTACT INFO</h2>
  <div class="col-photo" role="img" aria-label="Smiling support agent wearing a headset" style="background:linear-gradient(90deg,#e9e9e9,#dcdcdc 50%,#f4f4f4)"></div>
  <h3 class="contact-name">Velun Tresk ,PLLC</h3>
  <ul class="contact-list">
    <li>velun.tresk@tresklaw.example</li>
    <li>Telephone: 212.555.0186</li>
    <li>Fax: 212.555.0195</li>
    <li>Mailing Address:</li>
    <li>88 Harlow Lane, Brookvale, NY 10099</li>
  </ul>
</section>

<footer class="abs site-footer">
  <div class="abs fcol" style="left:123px"><h3>Quick Links</h3>
    <ul><li>Home</li><li>About Us</li><li>Services</li><li>Practices</li><li>News</li><li>FAQ's</li><li>Contact US</li></ul></div>
  <div class="abs fcol" style="left:284px"><h3>Services</h3>
    <ul><li>Intellectual Property</li><li>Patents</li><li>Copyrights</li><li>Trademarks</li><li>Trade secrets</li><li>Healthcare Compliance</li><li>Elder law</li><li>Wills</li><li>Trusts</li></ul></div>
  <div class="abs fcol" style="left:478px"><h3>Support Links</h3>
    <ul><li>Legal Notice</li><li>Privacy Policy</li><li>Terms &amp; Conditions</li><li>Help</li></ul></div>
  <div class="abs fcol" style="left:669px"><h3>Newsletter SignUp</h3>
    <p class="news-copy">Sign-up for our daily emails by entering your information below:</p>
    <div class="field" style="margin-top:14px">Name</div>
    <div class="field" style="margin-top:15px">Enter Your E-Mail ID</div>
    <div class="subscribe" style="margin:12px 0 0 120px">Subscribe</div></div>
  <div class="abs fcol" style="left:904px"><h3>Connect With Us</h3>
    <ul class="social">
      <li><span class="social-dot"></span>Chirpline</li>
      <li><span class="social-dot"></span>Friendwall</li>
      <li><span class="social-dot"></span>Worknet</li>
    </ul></div>
  <p class="abs copyright">Copyright ©2013 Company Name &nbsp; - All rights reserved</p>
</footer>

</body>
</html>
```